Business Card design for law firm = Brightvale Australia

We are seeking a new design for our business cards.
We are keeping our logo, which is attached.
We need space for
Name
Title
Address is , which is
Level 7
214 Marlowe Street
Sydney NSW 2047
Phone :
Mobile :
Fax :
Email :
DX :
website www.brightvale-example.com.au

Industry/Entity Type

Law Firm / Banking and Finance

Contact Information for Business Card

We are seeking a new design for our business cards. We are keeping our logo. We need space for Name Title Address is Level 7 214 Marlowe Street Sydney NSW 2047 Phone Mobile Fax Email DX website www.brightvale-example.com.au

Colors
0054AA
0677BA
7BADD7
CADEEF
E8F1F8

Requirements
Must have
• see our website for general feel www.brightvale-example.com.au

```html
<!DOCTYPE html>
<html lang="en">
<head>
<meta charset="utf-8">
<title>Brightvale Business Card</title>
<link href="https://fonts.googleapis.com/css2?family=Crimson+Text:wght@700&family=Roboto:wght@400&display=swap" rel="stylesheet">
<style>
  :root {
    --bg: #c4c4c4;
    --paper: #ffffff;
    --brand-blue: #1f5fad;
    --deep-blue: #0054aa;
    --cyan: #0a8fc4;
    --ink: #333333;
    --white: #ffffff;
  }
  * { box-sizing: border-box; margin: 0; padding: 0; }
  html, body {
    width: 1200px; height: 788px; overflow: hidden;
    background: var(--bg);
  }
  .stage { position: relative; width: 1200px; height: 788px; }
  .card {
    position: absolute; top: 229px;
    width: 540px; height: 330px;
    border-radius: 26px; overflow: hidden;
    box-shadow: 0 6px 18px rgba(0,0,0,.18);
  }
  .card-front { left: 45px; background: var(--paper); }
  .card-back { left: 615px; background: var(--brand-blue); }

  .accent-band {
    position: absolute; top: 0; right: 0;
    width: 118px; height: 100%;
    background: var(--cyan);
  }
  .side-marker {
    position: absolute; left: 0; top: 128px;
    width: 14px; height: 26px; background: var(--deep-blue);
  }
  .front-content {
    position: absolute; left: 36px; top: 32px;
    font-family: "Roboto", Arial, sans-serif; color: var(--ink);
  }
  .brand-name {
    font-family: "Roboto", Arial, sans-serif;
    font-weight: 400; font-size: 40px; line-height: 1;
    color: var(--deep-blue);
  }
  .person-name {
    margin-top: 52px;
    font-family: "Crimson Text", Georgia, serif;
    font-weight: 700; font-size: 21px; letter-spacing: 1px;
    color: var(--deep-blue); line-height: 1;
  }
  .person-title { font-size: 13.5px; margin-top: 4px; }
  .address { margin-top: 12px; font-size: 13.5px; line-height: 17px; }
  .contacts { margin-top: 10px; list-style: none; font-size: 13px; line-height: 17px; }
  .contacts li { display: flex; align-items: center; gap: 7px; }
  .contacts svg { width: 10px; height: 10px; fill: var(--deep-blue); flex: none; }

  .back-lockup {
    position: absolute; inset: 0;
    display: flex; align-items: center; justify-content: center;
  }
  .back-name {
    font-family: "Roboto", Arial, sans-serif;
    font-size: 54px; font-weight: 400; color: var(--white); line-height: 1;
  }
</style>
</head>
<body>
<main class="stage">
  <section class="card card-front">
    <div class="accent-band" role="img" aria-label="Cyan band with dark blue brush stroke accents"></div>
    <div class="side-marker"></div>
    <div class="front-content">
      <div class="brand-name">Brightvale</div>
      <div class="person-name">HELENA MARSH</div>
      <div class="person-title">Chief Legal Officer, BA, LLB (Hons)</div>
      <div class="address">Level 7, 214 Marlowe Street<br>Sydney NSW 2047</div>
      <ul class="contacts">
        <li><svg viewBox="0 0 10 10"><path d="M2 0.5 L3.8 2.6 L2.9 3.8 Q4 6 6.2 7.1 L7.4 6.2 L9.5 8 L8.3 9.5 Q4 9 0.5 1.7 Z"/></svg>02 5550 0142</li>
        <li><svg viewBox="0 0 10 10"><path d="M2.5 0 H7.5 V10 H2.5 Z M3.5 1.2 V7.8 H6.5 V1.2 Z"/></svg>02 5550 3871</li>
        <li><svg viewBox="0 0 10 10"><path d="M2.5 0 H7.5 V3 H2.5 Z M0.5 3.5 H9.5 V8 H0.5 Z M2.5 7 H7.5 V10 H2.5 Z"/></svg>02 5550 6409</li>
        <li><svg viewBox="0 0 10 10"><path d="M0 1.5 H10 V8.5 H0 Z M0.8 2.2 L5 5.6 L9.2 2.2"/></svg>helena.marsh@brightvale-example.com.au</li>
        <li><svg viewBox="0 0 10 10"><circle cx="5" cy="5" r="5"/></svg>www.brightvale-example.com.au</li>
      </ul>
    </div>
  </section>

  <section class="card card-back">
    <div class="back-lockup">
      <div class="back-name">Brightvale</div>
    </div>
  </section>
</main>
</body>
</html>
```